Fresh Dwelling Tract Guide needs a new Landing Page

I like to get a landing page or website with 2-3 pages to help target home buyers who are looking to buy homes from builders such as TW Residences, Morvik, P.L. Fennick, etc. The landing page/website to be non-cluttered and be able to explain to home buyers that there are many benefits to include me as their buyer's agent when they buy a brand new home from any builders.
I may want to incorporate a short explanation video (animated) on the landing page and then for the viewer to click on a button that will take them to another page where they can search for new homes from different builders.
Target Market(s)
Home buyers looking to buy brand new home from builders such as TW Residences, Morvik, P.L. Fennick, etc.
Industry/Entity Type
Real Estate
Number of Pages Required
2 page
Font styles to use
Requirements
Must have
- The landing page may have the explanation video at the bottom of the landing page (scrolled down) or there may be a CALL TO ACTION button that takes the viewer to the 2nd page to watch the explanation video. Once they watched the explanation video and are still interested, they can click on another CALL TO ACTION button that will take them to another website that they will be able to search for all the available new homes and register their contact information.
Should not have
- No clutters and no dark colors.

```html
<!DOCTYPE html>
<html lang="en">
<head>
<meta charset="UTF-8">
<title>Fresh Dwelling Tract — Search for New Homes</title>
<link rel="stylesheet" href="https://fonts.googleapis.com/css2?family=Oswald:wght@500;600&family=Roboto:wght@400;500&display=swap">
<style>
  :root {
    --white: #ffffff;
    --footer-bg: #f3f7fb;
    --footer-text: #2f4a66;
    --wave-blue: #2b86cf;
    --wave-light: #cfe3f4;
    --sky-top: #6e9bd0;
    --sky-mid: #a9c4e0;
    --town: #c9b99a;
    --green: #7fa98a;
    --water: #3aa7b4;
    --shade: rgba(30, 60, 100, 0.22);
  }
  * { margin: 0; padding: 0; box-sizing: border-box; }
  html, body {
    width: 1200px;
    height: 843px;
    overflow: hidden;
    background: var(--footer-bg);
  }
  .page {
    position: relative;
    width: 1200px;
    height: 843px;
    overflow: hidden;
    font-family: "Roboto", Arial, sans-serif;
    color: var(--white);
  }
  .hero-photo {
    position: absolute;
    inset: 0 0 100px 0;
    background:
      linear-gradient(var(--shade), var(--shade)),
      linear-gradient(180deg, var(--sky-top) 0%, var(--sky-mid) 40%, var(--town) 58%, var(--green) 70%, var(--water) 84%, #2f95a6 100%);
  }
  .site-header {
    position: absolute;
    top: 34px;
    left: 130px;
    right: 132px;
    display: flex;
    justify-content: space-between;
    align-items: flex-start;
  }
  .brand {
    font-family: "Oswald", Arial, sans-serif;
    font-weight: 500;
    font-size: 45px;
    line-height: 1;
    letter-spacing: 0.2px;
    text-shadow: 0 1px 6px rgba(20, 40, 70, 0.3);
  }
  .menu-toggle {
    margin-top: 12px;
    width: 37px;
    height: 32px;
    border: 2px solid var(--white);
    border-radius: 4px;
    display: flex;
    flex-direction: column;
    justify-content: center;
    gap: 4px;
    padding: 0 6px;
  }
  .menu-toggle span {
    display: block;
    height: 3px;
    background: var(--white);
    border-radius: 2px;
  }
  .hero-content {
    position: absolute;
    top: 213px;
    left: 0;
    width: 1200px;
    text-align: center;
    text-shadow: 0 1px 6px rgba(20, 40, 70, 0.35);
  }
  .play-button {
    display: block;
    margin: 0 auto;
    width: 62px;
    height: 62px;
  }
  .hero-title {
    margin-top: 22px;
    font-family: "Oswald", Arial, sans-serif;
    font-weight: 600;
    font-size: 52px;
    line-height: 1;
    letter-spacing: -1.5px;
    text-transform: uppercase;
  }
  .hero-text {
    width: 650px;
    margin: 26px auto 0;
    font-weight: 500;
    font-size: 14.3px;
    line-height: 25.6px;
  }
  .cta-button {
    display: inline-block;
    margin-top: 24px;
    width: 175px;
    height: 39px;
    line-height: 35px;
    border: 2px solid var(--white);
    border-radius: 20px;
    color: var(--white);
    text-decoration: none;
    font-weight: 500;
    font-size: 17px;
    text-transform: uppercase;
  }
  .footer-wave {
    position: absolute;
    left: 0;
    top: 0;
    width: 1200px;
    height: 843px;
  }
  .site-footer {
    position: absolute;
    top: 747px;
    left: 0;
    width: 1200px;
    text-align: center;
    color: var(--footer-text);
  }
  .social-links {
    display: flex;
    justify-content: center;
    gap: 3px;
  }
  .social-links a {
    width: 27px;
    height: 27px;
    border: 1.5px solid var(--footer-text);
    border-radius: 50%;
  }
  .copyright {
    margin-top: 20px;
    font-size: 13.6px;
    letter-spacing: 0.1px;
  }
  .copyright a { color: var(--footer-text); text-decoration: none; }
</style>
</head>
<body>
<div class="page">
  <div class="hero-photo" role="img" aria-label="Aerial photo of a waterfront marina with yachts and high-rise condominium towers under a cloudy blue sky"></div>

  <header class="site-header">
    <div class="brand">Fresh Dwelling Tract</div>
    <div class="menu-toggle" aria-label="Menu"><span></span><span></span><span></span></div>
  </header>

  <section class="hero-content">
    <svg class="play-button" viewBox="0 0 62 62" aria-label="Play video">
      <circle cx="31" cy="31" r="31" fill="#ffffff"/>
      <path d="M23 16 L47 31 L23 46 Z" fill="#2f4a66"/>
    </svg>
    <h1 class="hero-title">Search for new homes</h1>
    <p class="hero-text">Sed ut perspiciatis unde omnis iste natus error sit voluptatem accusantium doloremque laudantium, totam rem aperiam, eaque ipsa quae ab illo inventore veritatis et quasi architecto beatae vitae dicta sunt explicabo. Nemo enim ipsam voluptatem quia voluptas</p>
    <a class="cta-button" href="#">Get more info</a>
  </section>

  <svg class="footer-wave" viewBox="0 0 1200 843" aria-hidden="true">
    <path d="M0,683 C90,712 170,735 260,742 L440,742 C640,690 880,664 1040,664 C1090,664 1130,680 1155,698 L1200,700 L1200,843 L0,843 Z" fill="var(--wave-blue)"/>
    <path d="M0,698 C110,722 230,735 420,731 C650,726 900,690 1070,680 C1120,678 1160,692 1200,706 L1200,843 L0,843 Z" fill="var(--footer-bg)"/>
  </svg>

  <footer class="site-footer">
    <nav class="social-links" aria-label="Social links">
      <a href="#" aria-label="Social profile 1"></a>
      <a href="#" aria-label="Social profile 2"></a>
      <a href="#" aria-label="Social profile 3"></a>
      <a href="#" aria-label="Social profile 4"></a>
    </nav>
    <p class="copyright">© 2018 Fresh Dwelling Tract. All rights reserved. <a href="#">Privacy Policy</a>&nbsp; | &nbsp;<a href="#">Terms &amp; Conditions</a></p>
  </footer>
</div>
</body>
</html>
```